Redgum Ridge Towing website

We need a website design for a towing company based in Australia.
The design should be simple and minimalist. The site can be in colours of the logo are Blue, Red and White (see attached) - but we'd like to see options in some sort of industrial looking metallic theme if possible.
We base our business on our friendly and efficient customer service, the design should attempt to convey this in some way.

```html
<!DOCTYPE html>
<html lang="en">
<head>
<meta charset="utf-8">
<title>Redgum Ridge Towing</title>
<link href="https://fonts.googleapis.com/css2?family=Open+Sans:wght@300;400;600;700&display=swap" rel="stylesheet">
<style>
:root{
  --navy:#0b2756;
  --navy-deep:#08204a;
  --field:#0a2250;
  --red:#d4141d;
  --red-dark:#a80d14;
  --white:#ffffff;
  --text:#6b6b6b;
  --heading:#0d3470;
  --metal-a:#1c1f24;
  --metal-b:#3a4049;
}
*{box-sizing:border-box;margin:0;padding:0}
html,body{width:851px;height:1200px;overflow:hidden}
body{position:relative;background:var(--white);font-family:"Open Sans",sans-serif;color:var(--text)}
.abs{position:absolute}
.topbar{left:0;top:0;width:851px;height:32px;background:var(--navy-deep)}
.callnow{right:96px;top:9px;font-size:10.5px;color:#d6deea}
.callnow b{color:var(--white);font-weight:700;margin-right:4px}
.navbar{left:0;top:32px;width:851px;height:50px;background:linear-gradient(#f0202a,#c50f17 80%,#a50c12)}
.brand{left:90px;top:22px;display:flex;align-items:center;gap:6px;font-size:13px;font-weight:700;color:var(--white);z-index:2}
.brand .mark{width:18px;height:18px;border-radius:50%;background:var(--white)}
.nav{left:333px;top:32px;height:50px;display:flex}
.nav a{display:block;height:50px;line-height:50px;padding:0 11px;font-size:10.5px;font-weight:700;color:var(--white);text-decoration:none;border-left:1px solid rgba(0,0,0,.18)}
.hero{left:0;top:82px;width:851px;height:276px;background:radial-gradient(circle at 50% 40%,var(--metal-b),var(--metal-a) 75%)}
.slide{left:92px;top:98px;width:666px;height:236px;background:linear-gradient(100deg,#2b1a10 0%,#6b4522 30%,#c08a40 55%,#8a5a2a 80%,#3a2410 100%)}
.slide-copy{left:500px;top:174px;color:var(--white);font-weight:300;line-height:1.25}
.slide-copy .small{font-size:15px}
.slide-copy .big{font-size:20px;line-height:25px}
.btn-more{left:499px;top:248px;width:87px;height:25px;background:var(--navy);color:var(--white);font-size:9.5px;line-height:25px;text-align:center}
.dots{left:403px;top:311px;display:flex;gap:3px}
.dots i{width:10px;height:10px;border-radius:50%;background:var(--white)}
.dots i:first-child{background:var(--red)}
.welcome{left:92px;top:386px;width:436px}
.welcome h1{font-size:18.5px;font-weight:400;color:var(--heading);margin-bottom:28px}
.welcome p{font-size:9.8px;line-height:17px;margin-bottom:17px;hyphens:auto;-webkit-hyphens:auto}
.contact{left:547px;top:374px;width:211px;height:274px;background:var(--navy)}
.contact h2{position:absolute;left:12px;top:10px;font-size:18px;font-weight:400;color:var(--white)}
.field{position:absolute;left:13px;width:184px;height:30px;background:var(--field);color:#e6ebf3;font-size:10px;padding:8px 6px}
.submit{position:absolute;left:62px;top:227px;width:87px;height:25px;background:var(--red);color:var(--white);font-size:10px;font-weight:700;line-height:25px;text-align:center}
.services-title{left:0;top:676px;width:851px;text-align:center;font-size:18px;font-weight:400;color:var(--heading)}
.card{top:718px;width:155px}
.card .photo{width:155px;height:89px}
.card h3{font-size:10px;font-weight:700;color:#333;margin:8px 2px 7px}
.card p{font-size:9.5px;line-height:15.6px;hyphens:auto;-webkit-hyphens:auto}
.card .read{display:inline-block;margin-top:9px;width:62px;height:20px;line-height:20px;text-align:center;background:var(--red);color:var(--white);font-size:10px;font-weight:700;border:1px solid var(--red-dark)}
.footer{left:0;top:984px;width:851px;height:216px;background:radial-gradient(circle at 50% 30%,var(--metal-b),var(--metal-a) 80%)}
.footer-panel{left:86px;top:984px;width:680px;height:173px;background:var(--navy)}
.fcol{top:994px;color:var(--white)}
.fcol h4{font-size:13px;font-weight:400;margin-bottom:10px}
.fcol ul{list-style:none;font-size:8.5px;line-height:17px}
.fcol .intro{font-size:8.5px;line-height:14px;width:160px;margin-top:-4px}
.ninput{position:absolute;left:0;width:157px;height:19px;background:var(--white);border:1px solid #c9ced6;color:#888;font-size:8px;padding:3px 9px}
.subscribe{position:absolute;left:88px;top:120px;width:69px;height:18px;line-height:18px;text-align:center;border-radius:9px;background:var(--red);font-size:9px;font-weight:700}
.social{display:flex;align-items:center;justify-content:space-between;width:98px;height:20px;margin-bottom:6.5px;font-size:8.5px}
.social i{width:19px;height:19px;border-radius:50%;background:var(--white)}
.copyright{left:0;top:1174px;width:851px;text-align:center;font-size:8.5px;color:var(--white)}
</style>
</head>
<body>
<div class="abs topbar"></div>
<div class="abs callnow"><b>CALL NOW</b>1-300-555-0148</div>
<div class="abs navbar"></div>
<div class="abs brand"><span class="mark"></span>Redgum Ridge Towing</div>
<nav class="abs nav">
  <a href="#">HOME</a><a href="#">ABOUT US</a><a href="#">TOWING SERVICES</a><a href="#">GET A QUOTE</a><a href="#">CONTACT US</a>
</nav>

<div class="abs hero" role="img" aria-label="Dark perforated metal texture background"></div>
<div class="abs slide" role="img" aria-label="Tow truck pickup driving along a country road at sunset"></div>
<div class="abs slide-copy">
  <div class="small">WE PROVIDE TOWING SERVICE</div>
  <div class="big">AND CAR BREAKDOWN<br>SERVICE IN AUSTRALIA</div>
</div>
<div class="abs btn-more">KNOW MORE</div>
<div class="abs dots"><i></i><i></i><i></i><i></i></div>

<section class="abs welcome">
  <h1>Welcome to Redgum Ridge Towing</h1>
  <p>Lorem Ipsum is simply dummy text of the printing and typesetting industry. Lorem Ipsum has been the industry's standard dummy text ever since the 1500s, when an unknown printer took a galley of type and scrambled it to make a type specimen book. It has survived not only five centuries, but also the leap into electronic typesetting, remaining essentially unchanged. It was popularised in the 1960s with the release of Lettermark sheets containing Lorem Ipsum passages, and more recently with desktop publishing software like Pagecraft Studio</p>
  <p>Lorem Ipsum is simply dummy text of the printing and typesetting industry. Lorem Ipsum has been the industry's standard dummy text ever since the 1500s, when an unknown printer took a galley of type and scrambled it to make a type specimen book. It has survived not only five centuries, but also the leap into electronic typesetting, remaining essentially unchanged. It was popularised in the 1960s with the release of Lettermark sheets containing Lorem Ipsum passages .</p>
</section>

<aside class="abs contact">
  <h2>Contact US</h2>
  <div class="field" style="top:40px">Name</div>
  <div class="field" style="top:77px">E-Mail</div>
  <div class="field" style="top:114px">Phone</div>
  <div class="field" style="top:152px;height:67px">Message</div>
  <div class="submit">SUBMIT</div>
</aside>

<h2 class="abs services-title">Our Services</h2>
<div class="abs card" style="left:94px"><div class="photo" role="img" aria-label="Tilt tray truck carrying forklifts" style="background:linear-gradient(#8fb4d8,#c9c4b8 55%,#7a7a72)"></div><h3>Tilt Tray</h3><p>Lorem ipsum dolor sit amet, consectetur adipisicing elit, sed do eiusmod tempor incididunt ut labore et dolore magna aliqua. Ut enim ad minim veniam, quis nostrud exercitation ullamco</p><span class="read">Read More</span></div>
<div class="abs card" style="left:264px"><div class="photo" role="img" aria-label="Orange heavy towing truck" style="background:linear-gradient(#3c5a80,#d9752a 55%,#3a3a3a)"></div><h3>Heavy Towing</h3><p>Lorem ipsum dolor sit amet, consectetur adipisicing elit, sed do eiusmod tempor incididunt ut labore et dolore magna aliqua. Ut enim ad minim veniam, quis nostrud exercitation ullamco</p><span class="read">Read More</span></div>
<div class="abs card" style="left:434px"><div class="photo" role="img" aria-label="Recovery crew beside a red tow truck" style="background:linear-gradient(90deg,#b5271f,#7d9cc0 55%,#d6d6d2)"></div><h3>Recovery Specialist</h3><p>Lorem ipsum dolor sit amet, consectetur adipisicing elit, sed do eiusmod tempor incididunt ut labore et dolore magna aliqua. Ut enim ad minim veniam, quis nostrud exercitation ullamco</p><span class="read">Read More</span></div>
<div class="abs card" style="left:604px"><div class="photo" role="img" aria-label="Low loader truck carrying machinery" style="background:linear-gradient(#9db0c2,#c9b43a 55%,#555)"></div><h3>Semi-Tilts-Low Loaders</h3><p>Lorem ipsum dolor sit amet, consectetur adipisicing elit, sed do eiusmod tempor incididunt ut labore et dolore magna aliqua. Ut enim ad minim veniam, quis nostrud exercitation ullamco</p><span class="read">Read More</span></div>

<div class="abs footer" role="img" aria-label="Dark perforated metal texture background"></div>
<div class="abs footer-panel"></div>
<div class="abs fcol" style="left:92px"><h4>Quick Links</h4><ul><li>Home</li><li>About Us</li><li>Services</li><li>Service Plans</li><li>News</li><li>FAQ &amp; Wiki</li><li>Contact Us</li></ul></div>
<div class="abs fcol" style="left:263px"><h4>Support Links</h4><ul><li>Legal Notice</li><li>Privacy Policy</li><li>Terms &amp; Conditions</li><li>Help</li></ul></div>
<div class="abs fcol" style="left:434px;width:160px;height:140px"><h4>Newsletter SignUp</h4><p class="intro">Sign-up for our daily emails by entering your information below:</p><div class="ninput" style="top:64px">Name</div><div class="ninput" style="top:94px">Enter Your E-Mail ID</div><div class="subscribe">Subscribe</div></div>
<div class="abs fcol" style="left:660px"><h4>Connect With Us</h4>
  <div class="social"><i></i>Chirper</div>
  <div class="social"><i></i>Friendbook</div>
  <div class="social"><i></i>Worklink</div>
</div>
<div class="abs copyright">Copyright ©2013 Company Name - All rights reserved</div>
</body>
</html>
```